Aerial Imaging and photgraphy business card

Design a business card with eye catching aerial photo of country side / landscape with a drone in the foreground.
Also contact details.

Target Market(s)

Aerial Imaging photography

Industry/Entity Type

Advertising

Contact Information for Business Card

Rowland
0412965203
Website http://www.skywardvistaphoto.com.au/
email address : skywardvistaphoto.com.au

Colors
e8f1ca
cadf82
9bcb3c
33a6d7
85cae6
cee9f5

Requirements
Must have
• High res photo
• Korvane drone in the foreground Either T4200 and korvane Glidewing or both
Nice to have
• high resolution landscape country photo on the front of the card with a Korvane T4200 drone in the foreground.

```html
<!DOCTYPE html>
<html lang="en">
<head>
<meta charset="utf-8">
<title>Skyward Vista Photo – Business Card</title>
<link rel="stylesheet" href="https://fonts.googleapis.com/css2?family=Open+Sans:wght@400;600;700&display=swap">
<style>
  :root {
    --page-bg: #e9e7e4;
    --card-frost: #f4f3f1;
    --field-green: #72b51e;
    --field-green-dark: #5e9e12;
    --field-stripe: #86c42e;
    --back-black: #0c0c0c;
    --brand-red: #a8232a;
    --brand-faint: #c9c3c0;
    --text-light: #ffffff;
    --drone-body: #e6e8ea;
    --drone-shade: #b9bec4;
  }
  * { box-sizing: border-box; margin: 0; padding: 0; }
  html, body {
    width: 1200px; height: 900px; overflow: hidden;
    background: var(--page-bg);
    font-family: "Open Sans", Arial, sans-serif;
  }
  .canvas { position: relative; width: 1200px; height: 900px; }

  .card {
    position: absolute;
    width: 556px; height: 342px;
    background: var(--card-frost);
    overflow: hidden;
    box-shadow: 0 6px 18px rgba(0,0,0,0.12);
  }
  .card--front { left: 238px; top: 62px; }
  .card--back  { left: 460px; top: 518px; }

  .brand {
    position: absolute; left: 0; right: 0; top: 0; height: 185px;
    display: flex; align-items: center; justify-content: center; gap: 12px;
  }
  .brand__dot {
    width: 22px; height: 22px; border-radius: 50%;
    background: var(--brand-red);
  }
  .brand__name {
    font-weight: 700; font-size: 30px; letter-spacing: 0.5px;
    color: var(--brand-red); text-transform: uppercase;
  }
  .card--back .brand__dot { background: var(--brand-faint); }
  .card--back .brand__name { color: var(--brand-faint); }

  .field-band {
    position: absolute; left: 0; right: 0; bottom: 0; height: 157px;
    background: var(--field-green);
  }
  .field-stripes { position: absolute; left: 0; top: 0; }

  .contact-name {
    position: absolute; left: 22px; top: 83px;
    color: var(--text-light);
    white-space: nowrap;
  }
  .contact-name__person { font-weight: 600; font-size: 17px; line-height: 1.15; }
  .contact-name__role { font-weight: 400; font-size: 13.5px; line-height: 1.5; }

  .contact-list {
    position: absolute; left: 172px; top: 72px;
    list-style: none; color: var(--text-light);
    font-size: 14.5px; line-height: 20.5px;
    white-space: nowrap;
  }
  .contact-list li { display: flex; align-items: center; gap: 9px; }
  .contact-icon { width: 11px; height: 11px; flex: none; display: block; }

  .drone-photo {
    position: absolute;
    border-radius: 40% 40% 30% 30%;
    background: radial-gradient(ellipse at 50% 45%, var(--drone-body) 0%, var(--drone-shade) 60%, rgba(185,190,196,0) 72%);
  }
  .card--front .drone-photo { left: 318px; top: 20px; width: 212px; height: 72px; }

  .night-band {
    position: absolute; left: 0; right: 0; bottom: 0; height: 155px;
    background: var(--back-black);
  }
  .card--back .drone-photo { left: 146px; top: 38px; width: 266px; height: 82px; }
</style>
</head>
<body>
<main class="canvas">

  <section class="card card--front" aria-label="Business card front">
    <header class="brand">
      <span class="brand__dot"></span>
      <span class="brand__name">Skyward Vista Photo</span>
    </header>

    <div class="field-band">
      <svg class="field-stripes" width="556" height="157" viewBox="0 0 556 157" aria-hidden="true">
        <rect x="0" y="6" width="556" height="5" fill="var(--field-stripe)"/>
        <rect x="0" y="22" width="556" height="6" fill="var(--field-stripe)"/>
        <rect x="0" y="40" width="556" height="6" fill="var(--field-stripe)"/>
        <rect x="0" y="58" width="556" height="5" fill="var(--field-stripe)"/>
        <polygon points="330,157 556,70 556,157" fill="var(--field-green-dark)"/>
      </svg>

      <div class="drone-photo" role="img" aria-label="White hexacopter camera drone in flight"></div>

      <div class="contact-name">
        <p class="contact-name__person">ROWLAND HALE</p>
        <p class="contact-name__role">General Manager</p>
      </div>

      <ul class="contact-list">
        <li>
          <svg class="contact-icon" viewBox="0 0 12 12" aria-hidden="true"><path d="M2.5 1 L4.5 1 L5.2 3.6 L4 4.6 Q5.2 7 7.4 8 L8.4 6.8 L11 7.5 L11 9.5 Q10.5 11 9 11 Q1 10 1 2.5 Q1 1 2.5 1Z" fill="#fff"/></svg>
          <span>0412 965 203</span>
        </li>
        <li>
          <svg class="contact-icon" viewBox="0 0 12 12" aria-hidden="true"><rect x="1" y="2.5" width="10" height="7" fill="#fff"/><path d="M1 2.5 L6 6.5 L11 2.5" stroke="var(--field-green)" stroke-width="1" fill="none"/></svg>
          <span>info@skywardvistaphoto.com.au</span>
        </li>
        <li>
          <svg class="contact-icon" viewBox="0 0 12 12" aria-hidden="true"><circle cx="6" cy="6" r="5" fill="#fff"/><path d="M3.5 4 Q5 3 6 4.5 Q5 6 6.5 7.5 L5 9.5" stroke="var(--field-green)" stroke-width="1" fill="none"/></svg>
          <span>www.skywardvistaphoto.com.au</span>
        </li>
      </ul>
    </div>
  </section>

  <section class="card card--back" aria-label="Business card back">
    <header class="brand">
      <span class="brand__dot"></span>
      <span class="brand__name">Skyward Vista Photo</span>
    </header>
    <div class="night-band">
      <div class="drone-photo" role="img" aria-label="White hexacopter camera drone on a black background"></div>
    </div>
  </section>

</main>
</body>
</html>
```